Homemaking training schools needs a Business Card design

Designer, Hello!

No special requirements, good-looking enough.
--------------------------------------------------------------------------

Name: Marcus Dole
Chairman
Tel: 0574-71948263
Mobile: 13857420916
Email: kelvora@mailnest.example
Web: www.prt2019.example
Add: No.258, LanpingJie, BeiyuanQu, Ningbo, Zhejiang

LOGO
Ningbo PRT Homemaking Training School

Target Market(s)

pregnant women, mothers, infants, the elderly and families, including cleaning, cooking, nursing training.

Industry/Entity Type

Business

Contact Information for Business Card

Name: Marcus Dole
Chairman
Tel: 0574-71948263
Mobile: 13857420916
Email: kelvora@mailnest.example
Web: www.prt2019.example

LOGO

Font styles to use
Serif
Sans Serif
Decorative

Requirements
Nice to have
• Feels: clean, specifications, safety, comfort, warmth and happiness.

```html
<!DOCTYPE html>
<html lang="en">
<head>
<meta charset="utf-8">
<title>PeiRenTang Business Card</title>
<link href="https://fonts.googleapis.com/css2?family=Arimo:wght@400;700&display=swap" rel="stylesheet">
<style>
  :root {
    --page: #e9e6e1;
    --magenta: #e2157f;
    --magenta-deep: #a8125e;
    --blue: #2a78bd;
    --blue-light: #3a8ad0;
    --white: #ffffff;
    --ink-grey: #5a5a5a;
  }
  * { margin: 0; padding: 0; box-sizing: border-box; }
  html, body {
    width: 1200px; height: 950px; overflow: hidden;
    background: var(--page);
    font-family: "Arimo", Arial, sans-serif;
  }
  .card {
    position: absolute;
    left: 280px;
    width: 640px; height: 366px;
    border-radius: 4px;
    box-shadow: 0 10px 28px rgba(0,0,0,0.22);
    overflow: hidden;
  }
  .card--back {
    top: 70px;
    background: linear-gradient(120deg, var(--magenta) 0%, #d3137a 55%, var(--magenta-deep) 100%);
    color: var(--white);
  }
  .card--front { top: 500px; background: var(--white); }

  .company { position: absolute; left: 0; right: 0; text-align: center; }
  .company__name {
    font-weight: 700; font-size: 40px; line-height: 1; letter-spacing: 0.5px;
  }
  .company__tagline { font-size: 16px; font-weight: 400; margin-top: 10px; }

  .card--back .company { top: 130px; }
  .card--back .company__name,
  .card--back .company__tagline { color: var(--white); }
  .back__web {
    position: absolute; top: 248px; left: 0; right: 0; text-align: center;
    font-size: 16px; letter-spacing: 3px; color: var(--white);
  }

  .card--front .company { top: 68px; }
  .card--front .company__name { color: var(--blue); }
  .card--front .company__tagline { color: var(--ink-grey); }

  .front__band {
    position: absolute; left: 0; right: 0; top: 186px; bottom: 0;
    background: linear-gradient(180deg, var(--blue-light), var(--blue));
    border-top: 3px solid var(--magenta);
    color: var(--white);
  }
  .person { position: absolute; left: 34px; top: 22px; }
  .person__name { font-weight: 700; font-size: 21px; margin-bottom: 6px; }
  .person__role, .person__address { font-size: 16px; line-height: 1.4; }

  .contacts {
    position: absolute; right: 30px; bottom: 22px;
    list-style: none; text-align: right; font-size: 16px; line-height: 1.45;
  }
  .contacts li { display: flex; align-items: center; justify-content: flex-end; gap: 8px; }
  .contacts svg { width: 15px; height: 15px; fill: var(--white); flex: none; }
</style>
</head>
<body>

<section class="card card--back" aria-label="Business card back">
  <div class="company">
    <p class="company__name">PeiRenTang</p>
    <p class="company__tagline">Training &amp; Services</p>
  </div>
  <p class="back__web">www.prt2019.example</p>
</section>

<section class="card card--front" aria-label="Business card front">
  <div class="company">
    <p class="company__name">PeiRenTang</p>
    <p class="company__tagline">Training &amp; Services</p>
  </div>

  <div class="front__band">
    <div class="person">
      <p class="person__name">Marcus Dole</p>
      <p class="person__role">Chairman</p>
      <p class="person__address">No.258, LanpingJie<br>BeiyuanQu, Ningbo, Zhejiang</p>
    </div>

    <ul class="contacts">
      <li>0574-71948263
        <svg viewBox="0 0 16 16" aria-hidden="true"><path d="M2 5c0-2 2-3 6-3s6 1 6 3v1h-3V5H5v1H2z M4 7h8l2 6H2z"/></svg>
      </li>
      <li>13857420916
        <svg viewBox="0 0 16 16" aria-hidden="true"><path d="M4 1h8v14H4z M5.5 3v9h5V3z" fill-rule="evenodd"/></svg>
      </li>
      <li>kelvora@mailnest.example
        <svg viewBox="0 0 16 16" aria-hidden="true"><path d="M1 3h14v10H1z M2.5 4.5 8 9l5.5-4.5z" fill-rule="evenodd"/></svg>
      </li>
      <li>www.prt2019.example
        <svg viewBox="0 0 16 16" aria-hidden="true"><circle cx="8" cy="8" r="7"/><path d="M1 8h14M8 1c3 3 3 11 0 14M8 1c-3 3-3 11 0 14" stroke="#2a78bd" stroke-width="1.2" fill="none"/></svg>
      </li>
    </ul>
  </div>
</section>

</body>
</html>
```